Church needs a street sign design

We're a small church located in Silicon Valley, California. Our website is https://www.vgtmarlowfield.org/ and our address is 4817 Ferrow Ave, San Jose, California, 95873. You can look up our location on Google Maps to see the sign from Street View. I have uploaded an image of the street sign as well. The marquee, the top section of the sign, and the separating line between them both will be removed. We're seeking a design for a new backlit acrylic insert that will go on the front of the light box and the back of the lightbox. The acrylic sign will fill the entire external frame. In the future, we may build a decorative wood frame around the structural legs, as visualized in one of the uploaded files. The church's brand colors are: #003366 (dark blue), #ff6600 (vibrant orange), #228b22 (forest green). I have also uploaded the church's logo assets. Our primary font is Montserrat and the secondary is Poppins. You can deviate from these colors/fonts if the sign is still coherent with the rest of our branding. Our branding values are mission, truth, passion, and community (please do not put those words on the sign! They are just intended to guide the look of the design). The sign dimensions are 96" by 47.5". Keep in mind that the sign will be backlit on a busy street side. It will also be positioned next to an old-looking church building. We do NOT want a sign that looks traditional, old, or antiquated. Instead, we want a modern-looking sign that pairs well with our old building while helping it look more modern too. We would also like the web address clearly visible on the sign: vgtmarlowfield.org. If you have any questions, just let me know!

```html
<!DOCTYPE html>
<html lang="en">
<head>
<meta charset="utf-8">
<title>Marlowfield Community Church – Street Sign</title>
<link rel="stylesheet" href="https://fonts.googleapis.com/css2?family=Montserrat:wght@600&family=Poppins:wght@700;800&family=Yellowtail&display=swap">
<style>
  :root {
    --stage: #808080;
    --ink: #141414;
    --white: #ffffff;
    --orange: #ff6600;
    --navy: #0f3a73;
    --url-ink: #232323;
    --sky-top: #8a7a66;
    --sky-glow: #e9b36a;
    --city: #4a3d31;
    --night: #000000;
  }
  * { box-sizing: border-box; margin: 0; padding: 0; }
  html, body { width: 1200px; height: 994px; overflow: hidden; }
  body { background: var(--stage); position: relative; }

  .sign {
    position: absolute; left: 20px; top: 211px;
    width: 1160px; height: 572px; overflow: hidden;
    background: var(--night);
  }
  .sign__photo {
    position: absolute; inset: 0 0 90px 0;
    background:
      linear-gradient(180deg, rgba(0,0,0,0) 55%, var(--night) 92%),
      linear-gradient(180deg, var(--sky-top) 0%, var(--sky-glow) 22%, #d89a55 30%, var(--city) 42%, #3a2e24 70%);
  }

  .brand {
    position: absolute; top: 40px; left: 414px;
    display: flex; align-items: center; gap: 16px;
    color: var(--ink);
    font-family: "Montserrat", sans-serif; font-weight: 600;
  }
  .brand__mark { width: 30px; height: 30px; background: var(--ink); }
  .brand__name { line-height: 1; }
  .brand__name span { display: block; }
  .brand__name .line-1 { font-size: 38px; letter-spacing: 0.5px; }
  .brand__name .line-2 { font-size: 15.5px; letter-spacing: 0.6px; margin-top: 6px; }

  .headline {
    position: absolute; left: 0; right: 0; top: 238px;
    text-align: center; font-family: "Poppins", sans-serif; font-weight: 800;
    color: var(--white); font-size: 80px; line-height: 1; letter-spacing: -1px;
  }
  .subhead {
    position: absolute; left: 0; right: 0; top: 323px;
    text-align: center; font-family: "Poppins", sans-serif; font-weight: 800;
    color: var(--orange); font-size: 45px; line-height: 1; letter-spacing: -1.2px;
  }
  .tagline {
    position: absolute; left: 367px; top: 372px; width: 425px; height: 62px;
  }
  .tagline svg { position: absolute; inset: 0; }
  .tagline__text {
    position: absolute; inset: 0; display: flex; align-items: center; justify-content: center;
    font-family: "Yellowtail", cursive; color: var(--white); font-size: 36px; padding-left: 10px;
  }

  .url-band { position: absolute; left: 0; right: 0; bottom: 0; height: 118px; }
  .url-band svg { position: absolute; inset: 0; }
  .url-band__text {
    position: absolute; left: 0; right: 0; top: 33px; text-align: center;
    font-family: "Poppins", sans-serif; font-weight: 800; color: var(--url-ink);
    font-size: 58px; letter-spacing: 3px; line-height: 1;
  }
</style>
</head>
<body>
  <main class="sign">
    <div class="sign__photo" role="img" aria-label="Photo of a city skyline at sunset with mountains and a golden sky"></div>

    <div class="brand">
      <div class="brand__mark"></div>
      <div class="brand__name">
        <span class="line-1">MARLOWFIELD</span>
        <span class="line-2">COMMUNITY CHURCH</span>
      </div>
    </div>

    <h1 class="headline">MAKING DISCIPLES</h1>
    <p class="subhead">&amp; HELPING THE HELPLESS</p>

    <div class="tagline">
      <svg viewBox="0 0 425 62" preserveAspectRatio="none" aria-hidden="true">
        <path fill="var(--navy)" d="M14 6 L410 2 L402 14 L418 20 L406 30 L421 40 L404 50 L412 60 L20 58 L4 52 L16 44 L2 36 L14 28 L0 20 L12 12 Z"/>
      </svg>
      <div class="tagline__text">For the Glory of Christ</div>
    </div>

    <div class="url-band">
      <svg viewBox="0 0 1160 118" preserveAspectRatio="none" aria-hidden="true">
        <path fill="var(--white)" d="M0 14 L40 10 L70 16 L110 8 L150 14 L190 11 L230 18 L270 9 L320 15 L360 12 L400 20 L440 10 L490 16 L530 12 L580 19 L620 9 L660 15 L700 11 L740 18 L780 10 L830 16 L870 12 L910 20 L950 13 L990 18 L1030 6 L1070 14 L1110 4 L1160 10 L1160 118 L0 118 Z"/>
      </svg>
      <div class="url-band__text">www.vgtmarlowfield.org</div>
    </div>
  </main>
</body>
</html>
```